Etiketten-Design für Kräuterbonbon-Metalldose
Katrin Wolber hat sehr viel Talent. Das Design ist absolut kreativ.
Zielgruppe
Unsere Firma FelvoNat verkauft verschiedene Sorten Kräuterbonbons.
Wir brauchen ein Etikett, dass auf eine Metall-Dose (Durchmesser 10 cam, Höhe ca. 3 cm) geklebt wird.
Zielgruppe: jung-alt
Aufgabenstellung
Der Name unserer Kräuterbonbons ist Moospille.
Wir möchten, dass unsere Kunden, wenn sie das Etikett sehen einen Bezug zur Schweiz herstellen können.
Wir verwenden für unsere Bonbons unterschiedliche Kräuter für verschiedene Anwendungen:
Konkret sind erstmal 4 Dosen geplant:
-Kräutermischung aus 16 Kräuter gegen Husten
-Salbei gegen Halsschmerzen
-Anis gegen Magenschmerzen
-Zitrone/Ingwer für die Nerven
Vorderseite: Produktbeschreibung
Rückseite: unsere Herstellerangaben
Größenangaben der Dose: Durchmesser 10 cm, Höhe ca. 3 cm
Im Anhang habe ich Ihnen noch weitere/ genauere Informationen zur Verfügung bereitgestellt!

```html
<!DOCTYPE html>
<html lang="de">
<head>
<meta charset="utf-8">
<title>Moospille – Etiketten Kräuterbonbon-Dosen</title>
<link rel="stylesheet" href="https://fonts.googleapis.com/css2?family=Open+Sans:wght@600;700;800&display=swap">
<style>
  :root {
    --canvas-bg: #ffffff;
    --label-rim: #e4e7e8;
    --label-field: #f3f5f4;
    --on-band: #ffffff;
    --tone-husten: #a9d36b;
    --tone-hals: #a388c4;
    --tone-magen: #8e9f5d;
    --tone-nerven: #efb14a;
  }
  html, body {
    margin: 0;
    padding: 0;
    overflow: hidden;
    background: var(--canvas-bg);
  }
  .canvas {
    width: 1200px;
    height: 1200px;
    display: grid;
    grid-template-columns: 600px 600px;
    grid-template-rows: 600px 600px;
    place-items: center;
    font-family: "Open Sans", sans-serif;
  }
  .tin-label { width: 500px; height: 500px; display: block; }
  .tin-label--husten { --tone: var(--tone-husten); }
  .tin-label--hals { --tone: var(--tone-hals); }
  .tin-label--magen { --tone: var(--tone-magen); }
  .tin-label--nerven { --tone: var(--tone-nerven); }

  .rim { fill: var(--label-rim); }
  .field { fill: var(--label-field); }
  .band { fill: none; stroke: var(--tone); stroke-width: 52; }
  .badge { fill: var(--tone); }
  .brand-name {
    fill: var(--on-band);
    font-family: "Open Sans", sans-serif;
    font-weight: 800;
    font-size: 30px;
    letter-spacing: 0.5px;
  }
  .subline {
    fill: var(--on-band);
    font-family: "Open Sans", sans-serif;
    font-weight: 700;
    font-size: 21px;
    letter-spacing: 2px;
  }
  .badge-text {
    fill: var(--on-band);
    font-family: "Open Sans", sans-serif;
    font-weight: 800;
    font-size: 20px;
  }
  .badge-text .unit { font-size: 12px; font-weight: 700; }
  .title {
    fill: var(--tone);
    font-family: "Open Sans", sans-serif;
    font-weight: 800;
    font-size: 29px;
  }
  .title--small { font-size: 25px; }
</style>
</head>
<body>
<main class="canvas">

  <!-- Kräutermischung -->
  <svg class="tin-label tin-label--husten" viewBox="0 0 500 500" aria-label="Etikett Kräutermischung gegen Husten">
    <defs>
      <path id="arc-top-husten" d="M 60 250 A 190 190 0 0 1 440 250"/>
      <path id="arc-bottom-husten" d="M 60 250 A 190 190 0 0 0 440 250"/>
      <linearGradient id="herb-husten" x1="0" y1="0" x2="0" y2="1">
        <stop offset="0" stop-color="#9fcf7a"/><stop offset="1" stop-color="#3f8a3a"/>
      </linearGradient>
    </defs>
    <circle class="rim" cx="250" cy="250" r="245"/>
    <circle class="field" cx="250" cy="250" r="232"/>
    <circle class="band" cx="250" cy="250" r="190"/>
    <text class="brand-name" dominant-baseline="central"><textPath href="#arc-top-husten" startOffset="50%" text-anchor="middle">Moospille</textPath></text>
    <text class="subline" dominant-baseline="central"><textPath href="#arc-bottom-husten" startOffset="50%" text-anchor="middle">Schweizer Kräuterbonbon</textPath></text>
    <rect class="badge" x="40" y="282" width="100" height="42" rx="21"/>
    <text class="badge-text" x="90" y="310" text-anchor="middle">125G</text>
    <rect class="badge" x="340" y="150" width="130" height="42" rx="21"/>
    <text class="badge-text" x="405" y="178" text-anchor="middle">16 <tspan class="unit">pieces</tspan></text>
    <text class="title" text-anchor="middle">
      <tspan x="250" y="210">Kräutermischung</tspan>
      <tspan x="250" y="245">aus 16 Kräuter</tspan>
      <tspan x="250" y="280">gegen Husten</tspan>
    </text>
    <rect role="img" aria-label="Illustration frischer grüner Hustenkräuter" x="185" y="298" width="130" height="72" rx="20" fill="url(#herb-husten)"/>
  </svg>

  <!-- Salbei -->
  <svg class="tin-label tin-label--hals" viewBox="0 0 500 500" aria-label="Etikett Salbei gegen Halsschmerzen">
    <defs>
      <path id="arc-top-hals" d="M 60 250 A 190 190 0 0 1 440 250"/>
      <path id="arc-bottom-hals" d="M 60 250 A 190 190 0 0 0 440 250"/>
      <linearGradient id="herb-hals" x1="0" y1="0" x2="0" y2="1">
        <stop offset="0" stop-color="#9b8cc9"/><stop offset="1" stop-color="#6f8f6a"/>
      </linearGradient>
    </defs>
    <circle class="rim" cx="250" cy="250" r="245"/>
    <circle class="field" cx="250" cy="250" r="232"/>
    <circle class="band" cx="250" cy="250" r="190"/>
    <text class="brand-name" dominant-baseline="central"><textPath href="#arc-top-hals" startOffset="50%" text-anchor="middle">Moospille</textPath></text>
    <text class="subline" dominant-baseline="central"><textPath href="#arc-bottom-hals" startOffset="50%" text-anchor="middle">Schweizer Kräuterbonbon</textPath></text>
    <rect class="badge" x="40" y="282" width="100" height="42" rx="21"/>
    <text class="badge-text" x="90" y="310" text-anchor="middle">125G</text>
    <rect class="badge" x="340" y="150" width="130" height="42" rx="21"/>
    <text class="badge-text" x="405" y="178" text-anchor="middle">16 <tspan class="unit">pieces</tspan></text>
    <text class="title" text-anchor="middle">
      <tspan x="250" y="225">Salbei gegen</tspan>
      <tspan x="250" y="262">Halsschmerzen</tspan>
    </text>
    <rect role="img" aria-label="Illustration blühender Salbeizweig" x="185" y="290" width="130" height="80" rx="20" fill="url(#herb-hals)"/>
  </svg>

  <!-- Anis -->
  <svg class="tin-label tin-label--magen" viewBox="0 0 500 500" aria-label="Etikett Anis gegen Magenschmerzen">
    <defs>
      <path id="arc-top-magen" d="M 60 250 A 190 190 0 0 1 440 250"/>
      <path id="arc-bottom-magen" d="M 60 250 A 190 190 0 0 0 440 250"/>
      <linearGradient id="herb-magen" x1="0" y1="0" x2="0" y2="1">
        <stop offset="0" stop-color="#c9c7a0"/><stop offset="1" stop-color="#5d7a45"/>
      </linearGradient>
    </defs>
    <circle class="rim" cx="250" cy="250" r="245"/>
    <circle class="field" cx="250" cy="250" r="232"/>
    <circle class="band" cx="250" cy="250" r="190"/>
    <text class="brand-name" dominant-baseline="central"><textPath href="#arc-top-magen" startOffset="50%" text-anchor="middle">Moospille</textPath></text>
    <text class="subline" dominant-baseline="central"><textPath href="#arc-bottom-magen" startOffset="50%" text-anchor="middle">Schweizer Kräuterbonbon</textPath></text>
    <rect class="badge" x="40" y="282" width="100" height="42" rx="21"/>
    <text class="badge-text" x="90" y="310" text-anchor="middle">125G</text>
    <rect class="badge" x="340" y="150" width="130" height="42" rx="21"/>
    <text class="badge-text" x="405" y="178" text-anchor="middle">16 <tspan class="unit">pieces</tspan></text>
    <text class="title" text-anchor="middle">
      <tspan x="250" y="225">Anis gegen</tspan>
      <tspan class="title--small" x="250" y="260">Magenschmerzen</tspan>
    </text>
    <rect role="img" aria-label="Illustration Anispflanze mit Blüten und Sternanis" x="185" y="288" width="130" height="82" rx="20" fill="url(#herb-magen)"/>
  </svg>

  <!-- Zitrone/Ingwer -->
  <svg class="tin-label tin-label--nerven" viewBox="0 0 500 500" aria-label="Etikett Zitrone/Ingwer für die Nerven">
    <defs>
      <path id="arc-top-nerven" d="M 60 250 A 190 190 0 0 1 440 250"/>
      <path id="arc-bottom-nerven" d="M 60 250 A 190 190 0 0 0 440 250"/>
      <linearGradient id="herb-nerven" x1="0" y1="0" x2="1" y2="1">
        <stop offset="0" stop-color="#e3c39a"/><stop offset="0.55" stop-color="#f4dd4a"/><stop offset="1" stop-color="#5c9b46"/>
      </linearGradient>
    </defs>
    <circle class="rim" cx="250" cy="250" r="245"/>
    <circle class="field" cx="250" cy="250" r="232"/>
    <circle class="band" cx="250" cy="250" r="190"/>
    <text class="brand-name" dominant-baseline="central"><textPath href="#arc-top-nerven" startOffset="50%" text-anchor="middle">Moospille</textPath></text>
    <text class="subline" dominant-baseline="central"><textPath href="#arc-bottom-nerven" startOffset="50%" text-anchor="middle">Schweizer Kräuterbonbon</textPath></text>
    <rect class="badge" x="40" y="282" width="100" height="42" rx="21"/>
    <text class="badge-text" x="90" y="310" text-anchor="middle">125G</text>
    <rect class="badge" x="340" y="150" width="130" height="42" rx="21"/>
    <text class="badge-text" x="405" y="178" text-anchor="middle">16 <tspan class="unit">pieces</tspan></text>
    <text class="title" text-anchor="middle">
      <tspan x="250" y="225">Zitrone/Ingwer</tspan>
      <tspan x="250" y="262">für die Nerven</tspan>
    </text>
    <rect role="img" aria-label="Illustration Ingwerwurzel, Zitrone und Minzblätter" x="185" y="288" width="130" height="82" rx="20" fill="url(#herb-nerven)"/>
  </svg>

</main>
</body>
</html>
```